Vellisant - Quality health delivered at your door

Vellisant offers home and Community Based Services for adults who wish to continue live independently in their communities. We increase accessibility to health care, reduce health care delivery gap, reduce mortality and morbidity, reduce health while promoting healthy living in the comfort of our patients communities or homes.

We provide on site services and deliver high quality healthcare at your door. Our experienced physicians coordinate care with our certified nurse practitioners and provide chronic care management, physical therapy, rehabilitation and medications management.

Target Market(s)

Older population living in independent living facilities

Industry/Entity Type

Health Care

Contact Information for Business Card

Vellisant

Number of Pages Required

4 page

Font styles to use
Sans Serif

Colors

Designer to choose colors to be used in the design.

```html
<!DOCTYPE html>
<html lang="en">
<head>
<meta charset="utf-8">
<title>Vellisant – Quality health delivered at your door</title>
<link href="https://fonts.googleapis.com/css2?family=PT+Sans:wght@400;700&family=Marcellus&family=Cinzel:wght@700&display=swap" rel="stylesheet">
<style>
:root{
  --orange:#f7991c;
  --green:#3d5a0c;
  --green-dark:#2f470a;
  --text:#6b6b6b;
  --white:#ffffff;
  --light:#f2f2f2;
}
*{margin:0;padding:0;box-sizing:border-box}
html,body{width:1200px;height:2946px;overflow:hidden}
body{position:relative;background:var(--white);font-family:"PT Sans",Arial,sans-serif;color:var(--text)}
.abs{position:absolute}
.heading{font-family:"Marcellus",Georgia,serif}

/* header */
.brand{left:78px;top:12px;width:150px;text-align:center}
.brand-dot{display:block;width:64px;height:64px;border-radius:50%;background:var(--green);margin:0 auto 4px}
.brand-name{font-family:"Marcellus",Georgia,serif;font-size:22px;color:var(--green);letter-spacing:1px}
.social{top:8px;right:78px;display:flex;gap:6px}
.social span{width:42px;height:42px;border-radius:50%}
.phone{left:545px;top:58px;display:flex;align-items:center;gap:12px;font-size:26px;color:#222}
.phone-icon{width:46px;height:46px;border-radius:50%;background:var(--orange);display:flex;align-items:center;justify-content:center}
.search{left:760px;top:62px;width:362px;height:44px;border-radius:22px;background:var(--light);display:flex;align-items:center;padding-left:16px;font-size:14px;color:#666}
.search-btn{position:absolute;right:2px;top:2px;width:40px;height:40px;border-radius:50%;background:var(--green);display:flex;align-items:center;justify-content:center}

/* nav */
.nav{left:0;top:115px;width:1200px;height:62px;background:var(--orange)}
.nav ul{list-style:none;display:flex;height:62px;padding-left:78px}
.nav li{color:var(--white);font-size:14px;line-height:62px;padding:0 13px;text-transform:uppercase}
.nav li.active{background:var(--green)}

/* hero */
.hero{left:0;top:177px;width:1200px;height:520px;background:linear-gradient(90deg,#3e4c2a 0%,#5c7040 45%,#9aae82 70%,#c9d3bd 100%)}
.hero-shadow{left:140px;top:697px;width:920px;height:24px;background:radial-gradient(ellipse at top,rgba(0,0,0,.25),rgba(0,0,0,0) 70%)}
.hero-kicker{left:78px;top:288px;font-family:"Cinzel",serif;font-size:26px;font-style:italic;color:var(--orange)}
.hero-title{left:78px;top:340px;width:600px;font-family:"Cinzel",serif;font-size:35px;line-height:52px;color:var(--white);text-shadow:0 2px 4px rgba(0,0,0,.5)}
.btn{display:inline-block;background:var(--green);color:var(--white);border-radius:30px;text-transform:uppercase}
.hero-btn{left:78px;top:522px;width:187px;height:54px;line-height:54px;text-align:center;font-size:22px}
.dots{left:556px;top:662px;display:flex;gap:10px}
.dots span{width:16px;height:16px;border-radius:50%;border:2px solid var(--white)}
.dots span.on{background:var(--orange);border-color:var(--orange)}

/* welcome */
.video-frame{left:78px;top:780px;width:397px;height:300px;background:var(--green)}
.video{left:86px;top:792px;width:440px;height:323px;background:#111}
.video-still{left:0;top:0;width:440px;height:290px;background:linear-gradient(135deg,#8b6d52,#a7b48c 50%,#6d8a57)}
.video-bar{left:10px;top:298px;width:420px;height:14px;display:flex;align-items:center;gap:10px}
.welcome-kicker{left:562px;top:776px;font-size:22px;color:var(--orange)}
.welcome-title{left:562px;top:802px;font-size:42px;color:var(--green)}
.welcome-text{left:562px;top:866px;width:520px;font-size:14.5px;line-height:26px}
.welcome-text p+p{margin-top:12px}
.know-btn{left:562px;top:1047px;width:177px;height:57px;line-height:57px;text-align:center;font-size:20px}

/* services */
.services-bg{left:0;top:1178px;width:1200px;height:674px;background:linear-gradient(90deg,#4a5a2e,#6f8456 40%,#a9b79a 70%,#5e6e44)}
.services-panel{left:78px;top:1178px;width:417px;height:674px;background:var(--orange);text-align:center}
.services-kicker{margin-top:46px;font-size:21px;color:var(--white)}
.services-title{font-size:38px;color:var(--green);margin-top:4px}
.services-list{list-style:none;margin:22px 24px 0}
.services-list li{height:44px;line-height:44px;font-size:16px;color:var(--white);border-bottom:1px solid rgba(255,255,255,.25);text-transform:uppercase}
.services-list li:first-child{color:var(--green);font-weight:700}
.services-list li:last-child{border-bottom:none}

/* testimonials */
.center{left:0;width:1200px;text-align:center}
.t-kicker{top:1912px;font-size:21px;color:var(--orange)}
.t-title{top:1940px;font-size:38px;color:var(--green)}
.quote-mark{left:560px;top:2003px;width:80px;height:80px;border-radius:50%;border:3px solid var(--orange);display:flex;align-items:center;justify-content:center}
.t-text{left:160px;top:2096px;width:880px;text-align:center;font-size:14.5px;line-height:26px}
.arrow{top:2100px}
.client-photo{left:500px;top:2190px;width:66px;height:66px;border-radius:50%;background:linear-gradient(#e9e2d9,#c7b9a8)}
.client-name{left:582px;top:2198px;font-size:20px;color:var(--orange)}
.client-site{left:585px;top:2226px;font-size:14px;color:#999}

/* newsletter */
.newsletter{left:0;top:2329px;width:1200px;height:156px;background:var(--orange)}
.nl-title{left:76px;top:2356px;font-size:38px;color:var(--white);font-family:"Marcellus",Georgia,serif}
.nl-text{left:80px;top:2412px;width:320px;font-size:14px;line-height:22px;color:var(--white)}
.nl-input{left:402px;top:2380px;width:470px;height:56px;background:var(--white);display:flex;align-items:center;padding:0 18px;font-size:15px;color:#444;justify-content:space-between}
.nl-btn{left:886px;top:2380px;width:178px;height:56px;line-height:56px;text-align:center;font-size:20px}

/* footer */
.footer{left:0;top:2485px;width:1200px;height:398px;background:var(--green)}
.f-col{top:2520px;color:var(--white)}
.f-head{font-size:18px;text-transform:uppercase;margin-bottom:14px}
.f-list{list-style:none}
.f-list li{font-size:14px;line-height:27px}
.f-list li::before{content:"•";color:var(--orange);margin-right:8px}
.contact-row{display:flex;gap:16px;align-items:flex-start;font-size:14px;line-height:22px;margin-bottom:14px}
.contact-row svg{flex:none;margin-top:2px}
.c-name{color:var(--orange);font-weight:700}
.f-social{display:flex;gap:10px;margin-top:10px}
.f-social span{width:42px;height:42px;border-radius:50%;background:var(--orange)}
.f-brand{left:870px;top:2596px;width:240px;text-align:center}
.f-brand-dot{display:block;width:130px;height:130px;border-radius:50%;background:var(--orange);border:6px solid #1b1b1b;margin:0 auto 8px}
.f-brand-name{font-family:"Marcellus",Georgia,serif;font-size:36px;color:#1f2e06}
.bottom-bar{left:0;top:2883px;width:1200px;height:63px;background:var(--orange);text-align:center;line-height:63px;font-size:14px;color:#2a2a2a}
.bottom-bar b{color:#111}
</style>
</head>
<body>

<!-- header -->
<div class="abs brand"><span class="brand-dot"></span><span class="brand-name">VELLISANT</span></div>
<div class="abs social">
  <span style="background:#3b5998"></span><span style="background:#33aadd"></span><span style="background:#0e76a8"></span><span style="background:#d34836"></span>
</div>
<div class="abs phone">
  <span class="phone-icon"><svg width="22" height="22" viewBox="0 0 24 24"><path fill="#fff" d="M6.6 10.8a15 15 0 0 0 6.6 6.6l2.2-2.2c.3-.3.7-.4 1-.2 1.1.4 2.3.6 3.6.6.6 0 1 .4 1 1V20c0 .6-.4 1-1 1A17 17 0 0 1 3 4c0-.6.4-1 1-1h3.5c.6 0 1 .4 1 1 0 1.3.2 2.5.6 3.6.1.3 0 .7-.2 1z"/></svg></span>
  123 456 7890
</div>
<div class="abs search">Search...
  <span class="search-btn"><svg width="18" height="18" viewBox="0 0 24 24"><circle cx="10" cy="10" r="6.5" fill="none" stroke="#fff" stroke-width="2.5"/><path d="M15 15l6 6" stroke="#fff" stroke-width="2.5" stroke-linecap="round"/></svg></span>
</div>

<nav class="abs nav">
  <ul>
    <li class="active">Home</li><li>Assisted Living</li><li>Skilled Nursing</li><li>Independent Living</li><li>Services</li><li>Respite Care</li><li>Rehabilitation</li><li>Marlow Learning Center</li>
  </ul>
</nav>

<!-- hero -->
<div class="abs hero" role="img" aria-label="Photo of a caregiver walking with an older man in a wheelchair outdoors among trees"></div>
<div class="abs hero-shadow"></div>
<div class="abs hero-kicker">WE PROVIDE YOU</div>
<h1 class="abs hero-title">SERVICES AND DELIVER HIGH QUALITY HEALTHCARE AT YOUR DOOR</h1>
<a class="abs btn hero-btn">Contact Us</a>
<div class="abs dots"><span></span><span></span><span class="on"></span><span></span></div>

<!-- welcome -->
<div class="abs video-frame"></div>
<div class="abs video">
  <div class="abs video-still" role="img" aria-label="Video still of a nurse assisting an older woman with a walker in front of a house"></div>
  <div class="abs video-bar">
    <svg width="12" height="14" viewBox="0 0 12 14"><rect x="1" y="1" width="3" height="12" fill="#fff"/><rect x="7" y="1" width="3" height="12" fill="#fff"/></svg>
    <svg width="330" height="6"><rect width="330" height="6" fill="#444"/><rect width="8" height="6" fill="#ddd"/></svg>
    <svg width="16" height="14" viewBox="0 0 16 14"><path d="M1 5h4l5-4v12l-5-4H1z" fill="#fff"/></svg>
    <svg width="14" height="14"><rect x="1" y="1" width="12" height="12" fill="none" stroke="#fff" stroke-width="2"/></svg>
  </div>
</div>
<div class="abs welcome-kicker heading">WELCOME TO</div>
<h2 class="abs welcome-title heading">VELLISANT</h2>
<div class="abs welcome-text">
  <p>Vellisant offers home and Community Based Services for adults who wish to continue to live independently in the comfort of their communities.</p>
  <p>We provide on site services and deliver high quality healthcare at your door. Our experienced physicians coordinate care with our certified nurse practitioners and provide chronic care management, physical therapy, rehabilitation and medications management.</p>
</div>
<a class="abs btn know-btn">Know More</a>

<!-- services -->
<div class="abs services-bg" role="img" aria-label="Photo of a caregiver pushing an older woman in a wheelchair through a park"></div>
<section class="abs services-panel">
  <div class="services-kicker heading">WE PROVIDE YOU</div>
  <h2 class="services-title heading">OUR BEST SERVICES</h2>
  <ul class="services-list">
    <li>Comprehensive Primary Care</li><li>Coordination of Speciality Care</li><li>Chronic Disease Management</li><li>Transitional Care</li><li>Skilled Nursing Visits</li><li>Social Services Assessment</li><li>Home Health Assistance</li><li>Physical Therapy</li><li>Mental Health</li><li>Dental Health</li><li>Transportation</li>
  </ul>
</section>

<!-- testimonials -->
<div class="abs center t-kicker heading">TESTIMONIALS</div>
<h2 class="abs center t-title heading">WHAT OUR CLIENT SAY</h2>
<div class="abs quote-mark"><svg width="40" height="34" viewBox="0 0 40 34"><path fill="#f7991c" d="M2 34V20C2 9 7 3 16 1l2 5c-5 2-7 5-7 10h7v18zm20 0V20c0-11 5-17 14-19l2 5c-5 2-7 5-7 10h7v18z"/></svg></div>
<p class="abs t-text">" Lorem Ipsum is simply dummy text of the printing and typesetting industry. Lorem Ipsum has been the industry's standard dummy text ever since the 1500s, when an unknown printer took a galley of type and scrambled it to make a er since the 1500s, when an unknown printer &nbsp;type and scrambled it to make a er"</p>
<svg class="abs arrow" style="left:76px" width="16" height="50" viewBox="0 0 16 50"><path d="M14 2L2 25l12 23" fill="none" stroke="#bbb" stroke-width="2"/></svg>
<svg class="abs arrow" style="left:1108px" width="16" height="50" viewBox="0 0 16 50"><path d="M2 2l12 23L2 48" fill="none" stroke="#bbb" stroke-width="2"/></svg>
<div class="abs client-photo" role="img" aria-label="Client portrait"></div>
<div class="abs client-name heading">CLIENT NAME</div>
<div class="abs client-site">something.com</div>

<!-- newsletter -->
<div class="abs newsletter"></div>
<h2 class="abs nl-title">NEWSLETTER</h2>
<p class="abs nl-text">Receive exclusive access to articles, white papers and our regular monthly newsletter?</p>
<div class="abs nl-input">Enter Your Email*
  <svg width="24" height="20" viewBox="0 0 24 20"><path d="M2 5l20-3-3 16-7-5-4 4v-6z" fill="none" stroke="#555" stroke-width="1.5" stroke-linejoin="round"/></svg>
</div>
<a class="abs btn nl-btn">Subscribe</a>

<!-- footer -->
<footer class="abs footer"></footer>
<div class="abs f-col" style="left:78px">
  <div class="f-head">Site Map</div>
  <ul class="f-list"><li>Home</li><li>Assisted Living</li><li>Skilled Nursing</li><li>Independent Living</li><li>Services</li><li>Respite Care</li><li>Rehabilitation</li><li>Marlow LearningCenter</li><li>Marlow Learning</li></ul>
</div>
<div class="abs f-col" style="left:342px">
  <div class="f-head">Services</div>
  <ul class="f-list"><li>Comprehensive Primary Care</li><li>Coordination Of Speciality Care</li><li>Chronic Disease Management</li><li>Transitional Care</li><li>Skilled Nursing</li><li>Social Services Assessment</li><li>Home Health Assistance</li><li>Physical Therapy</li><li>Mental Health</li><li>Dental Health</li><li>Transportation</li></ul>
</div>
<div class="abs f-col" style="left:606px;width:230px">
  <div class="f-head">Contact Us</div>
  <div class="contact-row">
    <svg width="18" height="22" viewBox="0 0 18 22"><path d="M9 21s7-7.5 7-12.5A7 7 0 0 0 2 8.5C2 13.5 9 21 9 21z" fill="none" stroke="#f7991c" stroke-width="1.6"/><circle cx="9" cy="8.5" r="2.5" fill="none" stroke="#f7991c" stroke-width="1.6"/></svg>
    <div><div class="c-name">VELLISANT</div>101 - Lorem ipsum is simple dummy text of print and type setting industry.</div>
  </div>
  <div class="contact-row"><svg width="18" height="18" viewBox="0 0 24 24"><path d="M6.6 10.8a15 15 0 0 0 6.6 6.6l2.2-2.2c.3-.3.7-.4 1-.2 1.1.4 2.3.6 3.6.6.6 0 1 .4 1 1V20c0 .6-.4 1-1 1A17 17 0 0 1 3 4c0-.6.4-1 1-1h3.5c.6 0 1 .4 1 1 0 1.3.2 2.5.6 3.6.1.3 0 .7-.2 1z" fill="none" stroke="#f7991c" stroke-width="1.6"/></svg><b>123 456 7890</b></div>
  <div class="contact-row"><svg width="18" height="14" viewBox="0 0 18 14"><rect x="1" y="1" width="16" height="12" fill="none" stroke="#f7991c" stroke-width="1.5"/><path d="M1 1l8 7 8-7" fill="none" stroke="#f7991c" stroke-width="1.5"/></svg>info@vellisant.com</div>
  <div class="contact-row"><svg width="18" height="18" viewBox="0 0 18 18"><circle cx="9" cy="9" r="8" fill="none" stroke="#f7991c" stroke-width="1.5"/><ellipse cx="9" cy="9" rx="3.5" ry="8" fill="none" stroke="#f7991c" stroke-width="1.2"/><path d="M1 9h16" stroke="#f7991c" stroke-width="1.2"/></svg>www.vellisant.com</div>
  <div class="f-social"><span></span><span></span><span></span><span></span></div>
</div>
<div class="abs f-brand"><span class="f-brand-dot"></span><span class="f-brand-name">VELLISANT</span></div>

<div class="abs bottom-bar">© <b>VELLISANT</b> - 2017 All rights reserved.</div>

</body>
</html>
```